Business card for Luxury Portable Restroom Trailer company

We are a Luxury Portable Restroom Trailer Company Called FALCRIDGE HIRES. Based in Orange County California. We provide portable restroom trailers for events, such as, Weddings, Concerts, Charity events, Sporting events, Tournaments, Corporate events, ect. We rent and Sell the Luxury restrooms. Our colors are white, grey, and Orange. As you will see in the logo we uploaded.
There are 2 people in the company so the names and titles will change for the 3 people but card will remain the same. Here is the information for each Person: Dwight Penner CFO 555 318-0476
next Person: Leon Marchetti VP 555 318-0476
Next Person: Owen Marchetti CEO 555 318-0476
Information to include on the card: Luxury Restroom Trailers Rental and Sales. Weddings, Concerts, Charity, Sporting and Corp. Events.

```html
<!DOCTYPE html>
<html lang="en">
<head>
<meta charset="utf-8">
<title>Falcridge Hires – Business Card</title>
<link href="https://fonts.googleapis.com/css2?family=Montserrat:wght@400;500;700&family=Open+Sans:wght@400&display=swap" rel="stylesheet">
<style>
  :root {
    --backdrop: #d6d6d6;
    --grey-card-light: #8a8a8c;
    --grey-card-dark: #545456;
    --orange-light: #e98e5e;
    --orange: #dc5f22;
    --white: #ffffff;
    --charcoal: #4a4a4c;
  }
  * { margin: 0; padding: 0; box-sizing: border-box; }
  html, body { width: 1200px; height: 1200px; overflow: hidden; }
  body {
    background: var(--backdrop);
    font-family: "Montserrat", sans-serif;
    position: relative;
  }
  .card {
    position: absolute;
    left: 250px;
    width: 700px;
    height: 400px;
    border-radius: 22px;
    box-shadow: 0 8px 24px rgba(0,0,0,0.18);
    color: var(--white);
  }
  .card--front {
    top: 170px;
    background: linear-gradient(100deg, var(--grey-card-light) 0%, var(--grey-card-dark) 70%);
  }
  .card--back {
    top: 630px;
    background: linear-gradient(100deg, var(--orange-light) 0%, var(--orange) 50%);
  }
  .wordmark {
    font-family: "Montserrat", sans-serif;
    font-weight: 700;
    color: var(--white);
    letter-spacing: 0.04em;
    white-space: nowrap;
  }
  .card--front .wordmark {
    position: absolute;
    top: 120px;
    left: 0;
    width: 100%;
    text-align: center;
    font-size: 56px;
  }
  .tagline {
    position: absolute;
    top: 250px;
    left: 0;
    width: 100%;
    text-align: center;
    font-family: "Open Sans", sans-serif;
    font-size: 17px;
    line-height: 1.45;
    letter-spacing: 0.02em;
  }
  .card--back .wordmark {
    position: absolute;
    top: 52px;
    right: 44px;
    font-size: 30px;
  }
  .contact {
    position: absolute;
    left: 70px;
    bottom: 48px;
  }
  .contact__name { font-size: 30px; font-weight: 700; }
  .contact__title { font-size: 17px; font-weight: 400; margin: 4px 0 12px 12px; }
  .contact__row {
    display: flex;
    align-items: center;
    gap: 12px;
    font-size: 18px;
    font-weight: 500;
    margin: 6px 0 0 12px;
  }
  .contact__row svg { width: 16px; height: 16px; flex: none; }
  .address {
    position: absolute;
    right: 60px;
    bottom: 150px;
    text-align: right;
    font-size: 18px;
    font-weight: 500;
    line-height: 1.4;
  }
</style>
</head>
<body>
  <section class="card card--front">
    <div class="wordmark">FALCRIDGE HIRES</div>
    <p class="tagline">Luxury Restroom | Trailers Rental and Sales | Weddings |<br>Concerts | Charity | Sporting and Corp. Events</p>
  </section>

  <section class="card card--back">
    <div class="wordmark">FALCRIDGE HIRES</div>
    <div class="contact">
      <div class="contact__name">Dwight Penner</div>
      <div class="contact__title">CFO</div>
      <div class="contact__row">
        <svg viewBox="0 0 24 24" fill="#fff" aria-hidden="true"><path d="M6.6 10.8a15 15 0 0 0 6.6 6.6l2.2-2.2c.3-.3.7-.4 1-.2 1.1.4 2.3.6 3.6.6.6 0 1 .4 1 1V20c0 .6-.4 1-1 1A17 17 0 0 1 3 4c0-.6.4-1 1-1h3.5c.6 0 1 .4 1 1 0 1.3.2 2.5.6 3.6.1.3 0 .7-.2 1z"/></svg>
        <span>555 318-0476</span>
      </div>
      <div class="contact__row">
        <svg viewBox="0 0 24 24" fill="#fff" aria-hidden="true"><path d="M2 5h20v14H2z M2 5l10 8 10-8" stroke="#dc5f22" stroke-width="1.5"/></svg>
        <span>info@falcridgehires.com</span>
      </div>
      <div class="contact__row">
        <svg viewBox="0 0 24 24" aria-hidden="true"><circle cx="12" cy="12" r="10" fill="#fff"/><path d="M2 12h20M12 2c3 3 3 17 0 20M12 2c-3 3-3 17 0 20" stroke="#dc5f22" stroke-width="1.5" fill="none"/></svg>
        <span>www.falcridgehires.com</span>
      </div>
    </div>
    <div class="address">4780 Birchel Road<br>Lake Vennick Maine 11460</div>
  </section>
</body>
</html>
```